3 Page Design for Ninth Bay Capital

We want a Home Page, About Page, and Products & Services Page for Ninth Bay Capital. Please refer to the attached docs for more info.
If done in Figma, would like Figma files that can easily be ported to Wordpress.

```html
<!DOCTYPE html>
<html lang="en">
<head>
<meta charset="utf-8">
<title>Ninth Bay Capital — Home</title>
<link href="https://fonts.googleapis.com/css2?family=Inter+Tight:wght@300;400;500;700;800;900&display=swap" rel="stylesheet">
<style>
:root{
  --ink:#1c1c1e;
  --text:#3a3a3c;
  --crimson:#8b1630;
  --purple:#5b4a8e;
  --taupe:#8a7a5e;
  --sand:#e9e4da;
  --bar:#1d1d1f;
  --grey:#6d6d70;
  --line:#d9d9d9;
}
*{margin:0;padding:0;box-sizing:border-box}
html,body{width:1200px;height:4107px;overflow:hidden}
body{position:relative;background:#fff;font-family:"Inter Tight",Arial,sans-serif;color:var(--text)}
.abs{position:absolute}
.btn{position:absolute;display:flex;align-items:center;justify-content:center;color:#fff;font-weight:700;font-size:16px;letter-spacing:-.2px;border-radius:4px;text-transform:uppercase}
.btn-crimson{background:var(--crimson)}
.btn-purple{background:var(--purple)}
h1,h2{color:var(--ink);font-weight:800;letter-spacing:-1.5px;text-transform:uppercase}

.topbar{left:569px;top:0;width:631px;height:45px;background:var(--bar);border-bottom-left-radius:40px;display:flex;align-items:center;padding-left:52px;gap:22px;color:#fff;font-size:13px;letter-spacing:-.3px}
.topbar .item{display:flex;align-items:center;gap:14px}
.topbar .ic{width:30px;height:30px;border-radius:50%;background:#fff;display:flex;align-items:center;justify-content:center}
.topbar .sep{width:1px;height:28px;background:#666;margin:0 4px}

.brand{left:143px;top:52px;display:flex;align-items:center;gap:12px;font-weight:800;font-size:22px;color:var(--ink);letter-spacing:-.3px;text-transform:uppercase}
.brand .dot{width:44px;height:44px;border-radius:50%;background:var(--taupe)}
.nav{left:507px;top:108px;display:flex;gap:30px;font-size:15px;font-weight:700;color:var(--ink);text-transform:uppercase;letter-spacing:-.2px}
.nav .active{border-bottom:2px solid var(--ink);padding-bottom:1px}

.hero{left:0;top:150px;width:1200px;height:631px;background:linear-gradient(90deg,#f3f3f4 0%,#f7f7f8 45%,#e6e6e8 100%)}
.hero-sub{left:145px;top:488px;font-size:30px;font-weight:300;color:var(--ink);letter-spacing:-1px}
.dots{left:146px;top:692px;display:flex;gap:16px}
.dots span{width:8px;height:8px;border-radius:50%;background:#bbb}
.dots span:first-child{background:var(--ink)}
.hero-art{left:653px;top:215px;width:547px;height:540px;border-radius:50% 0 0 50%;background:radial-gradient(circle at 55% 50%,#6c6a64 0%,#4a4945 45%,#cfcfcf 75%,#ececec 100%)}

.mission{left:143px;top:781px;width:1057px;height:449px;border-radius:96px 0 0 96px;background:linear-gradient(90deg,#f2f0ec 0%,#e3ddd1 45%,#a59678 85%,#8b7a5c 100%);text-align:center}
.mission h2{position:absolute;left:114px;width:780px;top:80px;font-size:54px}
.mission p{position:absolute;left:104px;width:800px;top:155px;font-size:20px;line-height:38px;letter-spacing:-.7px;font-weight:400;color:var(--text)}

.story h2{position:absolute;left:143px;top:1370px;font-size:54px}
.story-photo{left:183px;top:1491px;width:364px;height:364px;border-radius:50%;background:linear-gradient(160deg,#8a8f98 0%,#c9c3b8 45%,#e9ecf0 70%,#7d8a9c 100%)}
.story p{position:absolute;left:658px;top:1372px;width:397px;font-size:20px;line-height:37.6px;letter-spacing:-.7px;text-align:justify;color:var(--text)}

.offer{left:0;top:1995px;width:1200px;height:1000px;border-radius:240px 240px 0 0;background:linear-gradient(180deg,#c9bda6 0%,#e6e0d4 12%,#ffffff 28%)}
.offer-title{left:0;width:1200px;top:2110px;text-align:center;font-size:54px}
.card{position:absolute;width:342px;border-radius:32px;overflow:hidden}
.card-row1{top:2231px;height:370px}
.card-row2{top:2617px;height:368px}
.c1{left:69px}.c2{left:429px}.c3{left:789px}
.card-info{left:462px;top:2265px;width:276px;height:302px;background:rgba(255,255,255,.93);border-radius:28px;text-align:center;padding-top:50px}
.card-info h3{font-size:18px;font-weight:700;color:var(--ink);line-height:28px;text-transform:uppercase;letter-spacing:-.4px}
.card-info p{font-size:15px;line-height:28px;color:var(--grey);letter-spacing:-.5px;margin-top:8px;padding:0 30px}

.cta{left:0;top:3213px;width:1053px;height:449px;border-radius:0 96px 96px 0;background:linear-gradient(90deg,#8b7a5c 0%,#bdb19b 35%,#e5e0d6 70%,#efece6 100%);text-align:center}
.cta h2{position:absolute;left:0;width:100%;top:100px;font-size:54px}
.cta p{position:absolute;left:0;width:100%;top:190px;font-size:24px;line-height:37px;font-weight:400;letter-spacing:-.8px;color:var(--text)}

.contact{position:absolute;top:3757px;width:260px;margin-left:-130px;text-align:center}
.contact .ic{width:72px;height:72px;border-radius:50%;border:2px solid #9a9a9a;margin:0 auto;display:flex;align-items:center;justify-content:center}
.contact .ic.on{background:var(--purple);border-color:var(--purple)}
.contact h4{margin-top:26px;font-size:16px;font-weight:700;color:var(--ink);text-transform:uppercase;letter-spacing:-.3px}
.contact p{margin-top:10px;font-size:14px;line-height:21px;color:var(--grey);letter-spacing:-.4px}

.rule{left:143px;top:3989px;width:912px;height:1px;background:var(--line)}
.legal{left:143px;top:4044px;font-size:14px;color:var(--grey);letter-spacing:-.4px}
.social{left:877px;top:4036px;display:flex;gap:14px}
.social span{width:34px;height:34px;border-radius:50%;background:var(--grey)}
</style>
</head>
<body>

<div class="abs topbar">
  <div class="item"><span class="ic"><svg width="14" height="14" viewBox="0 0 24 24"><path fill="#1d1d1f" d="M6.6 10.8a15.1 15.1 0 0 0 6.6 6.6l2.2-2.2a1 1 0 0 1 1-.25 11.4 11.4 0 0 0 3.6.57 1 1 0 0 1 1 1V20a1 1 0 0 1-1 1A17 17 0 0 1 3 4a1 1 0 0 1 1-1h3.5a1 1 0 0 1 1 1c0 1.25.2 2.45.57 3.57a1 1 0 0 1-.25 1z"/></svg></span>Call Us : +1 888 888 8888</div>
  <span class="sep"></span>
  <div class="item"><span class="ic"><svg width="14" height="14" viewBox="0 0 24 24"><path fill="#1d1d1f" d="M3 5h18v14H3z"/><path fill="none" stroke="#fff" stroke-width="2" d="M3 6l9 7 9-7"/></svg></span>info@companyname.com</div>
</div>

<div class="abs brand"><span class="dot"></span>Ninth Bay Capital</div>

<nav class="abs nav"><span class="active">Home</span><span>About</span><span>Products</span><span>Services</span></nav>
<div class="btn btn-crimson" style="left:904px;top:94px;width:150px;height:49px;font-size:15px">Get Started</div>

<section class="abs hero"></section>
<div class="abs hero-art" role="img" aria-label="Sprinting athlete in mid-stride over a dark backdrop and faint stock chart"></div>
<h1 class="abs" style="left:143px;top:245px;font-size:52px;line-height:73px">Built for Legacy.<br>Designed for<br>Performance.</h1>
<div class="abs hero-sub">Your Next Chapter Starts Now</div>
<div class="btn btn-purple" style="left:145px;top:575px;width:171px;height:58px">Get Started</div>
<div class="abs dots"><span></span><span></span><span></span><span></span></div>

<section class="abs mission">
  <h2>Our Mission</h2>
  <p>Technical Refined' positions Ninth Bay at the intersection of performance and sophistication. The design system communicates trust, discipline, and modernity — aligning perfectly with Ninth Bay's mission to help athletes and entrepreneurs create generational success.</p>
  <div class="btn btn-crimson" style="left:418px;top:303px;width:171px;height:57px">Read More</div>
</section>

<section class="story">
  <h2>Visual Story</h2>
  <div class="abs story-photo" role="img" aria-label="Smiling businesswoman at a desk with a laptop showing charts"></div>
  <p>Sed ut perspiciatis unde omnis iste natus error sit voluptatem accusaque ipsa quae ab illo inventore veritatis et quasi architecto beatae vitae dicta su dolores eos qui ratione voluptatem sequi nesciunt. Neque porro quisquam est, qui dolorem ipsum quia dolor sit amet, consectetur, adipisci velit, sed quia non numquansectetur, adipisci velit, sed quia non numquam eius m eius modi tempora incidunt ut labore et dolore magnam aliquam quaerat voluptatem.</p>
  <div class="btn btn-crimson" style="left:658px;top:1782px;width:171px;height:57px">Read More</div>
</section>

<section class="abs offer"></section>
<h2 class="abs offer-title">Offer Framework</h2>
<div class="card card-row1 c1" role="img" aria-label="Athletic woman in sportswear, black and white portrait" style="background:linear-gradient(160deg,#ececec,#9b9b9b 60%,#d4d4d4)"></div>
<div class="card card-row1 c2" role="img" aria-label="Blurred urban backdrop behind the info card" style="background:linear-gradient(160deg,#d8d8d8,#a9a9a9)"></div>
<div class="card card-row1 c3" role="img" aria-label="Hands on a laptop with floating financial dashboard graphics" style="background:linear-gradient(160deg,#3e5f8a,#1d2c44 60%,#6f7f95)"></div>
<div class="card card-row2 c1" role="img" aria-label="Woman sprinting outdoors beside stadium steps under a blue sky" style="background:linear-gradient(180deg,#4e83c4 0%,#a9c6e6 40%,#6b6f74 60%,#c6c3bd 100%)"></div>
<div class="card card-row2 c2" role="img" aria-label="Smiling woman with curly hair, arms crossed, in a bright office" style="background:linear-gradient(160deg,#a9bccf,#c9a98a 55%,#e4e2de)"></div>
<div class="card card-row2 c3" role="img" aria-label="Businessman with a laptop in front of a chalkboard of sketched ideas" style="background:linear-gradient(160deg,#3b3d40,#1f2022 60%,#4b4d50)"></div>
<div class="abs card-info">
  <h3>Lorem Ipsum<br>Doldor Sit</h3>
  <p>Nemo enim ipsam voluptate m quia voluptas sit aspernatur a ut odit ansequuntur</p>
  <div class="btn btn-purple" style="left:69px;top:212px;width:138px;height:46px">Read More</div>
</div>
<div class="btn btn-crimson" style="left:515px;top:3049px;width:170px;height:57px">View More</div>

<section class="abs cta">
  <h2>Ready to Get Started</h2>
  <p>Nemo enim ipsam voluptatem quia voluptas sit aspernatur<br>aut odit aut fugitsed quia consequuntur</p>
  <div class="btn btn-crimson" style="left:467px;top:296px;width:171px;height:58px">Get Started</div>
</section>

<div class="contact" style="left:218px"><div class="ic"><svg width="26" height="26" viewBox="0 0 24 24"><path fill="#777" d="M6.6 10.8a15.1 15.1 0 0 0 6.6 6.6l2.2-2.2a1 1 0 0 1 1-.25 11.4 11.4 0 0 0 3.6.57 1 1 0 0 1 1 1V20a1 1 0 0 1-1 1A17 17 0 0 1 3 4a1 1 0 0 1 1-1h3.5a1 1 0 0 1 1 1c0 1.25.2 2.45.57 3.57a1 1 0 0 1-.25 1z"/></svg></div><h4>Phone</h4><p>(+428) 888 888 8888</p></div>
<div class="contact" style="left:445px"><div class="ic"><svg width="24" height="28" viewBox="0 0 24 28"><path fill="#777" d="M12 0a10 10 0 0 0-10 10c0 7.5 10 18 10 18s10-10.5 10-18A10 10 0 0 0 12 0zm0 14a4 4 0 1 1 0-8 4 4 0 0 1 0 8z"/></svg></div><h4>Head Office</h4><p>123 west Dummy Car Street, Old City,<br>New State, USA. PO 4288</p></div>
<div class="contact" style="left:722px"><div class="ic on"><svg width="24" height="28" viewBox="0 0 24 28"><path fill="#fff" d="M12 0a10 10 0 0 0-10 10c0 7.5 10 18 10 18s10-10.5 10-18A10 10 0 0 0 12 0zm0 14a4 4 0 1 1 0-8 4 4 0 0 1 0 8z"/></svg></div><h4>Main Office</h4><p>123 west Dummy Car Street, Old City,<br>New State, USA. PO 4288</p></div>
<div class="contact" style="left:970px"><div class="ic"><svg width="28" height="22" viewBox="0 0 28 22"><rect width="28" height="22" rx="2" fill="#777"/><path d="M1 2l13 10 13-10" fill="none" stroke="#fff" stroke-width="2"/></svg></div><h4>Email</h4><p>info@companyname.com</p></div>

<div class="abs rule"></div>
<div class="abs legal">© 2025 Companyname. All Rights Reserved &nbsp;|&nbsp; Privacy Policy &nbsp;|&nbsp; Terms of Use</div>
<div class="abs social" aria-label="Social links"><span></span><span></span><span></span><span></span></div>

</body>
</html>
```